A new updated business card. A good first impression for new customers to our business.

I need something unique. I will attached a picture of our old rubbish cards, and also our current Logo ( I think this needs an update if you have any ideas, its very basic and budget)The best way you will get to see my business is checking our Facebook page, I don't really know what else to say, but anything you want to know, ask away.www.facebook.com/tkwashandseal/

Target Market(s)

Home owners

Industry/Entity Type

Business

Contact Information for Business Card

T&K's Pressure Cleaning & Concrete Sealing
Maya 0492 615 370 maya@tkwashandseal.com
Dylan 0431 528 906 dylan@tkwashandseal.com

FB: www.facebook.com/tkwashandseal/
Website: www.tkwashandseal.net (This is pretty rubbish- we don't really use it)

100% customer satisfaction guaranteed

All aspects of Hi-Pressure Cleaning
Sealing & Re-Sealing
Roof Cleaning
Colour sealing
Decorative coatings

Free no obligation quotes

Requirements
Must have
• NO OBLIGATION FREE quotes
• 100% Customer satisfaction guaranteed
• Can you please add both names, contact details and email address on one card.
• Dylan 0431 528 906
• dylan@tkwashandseal.com
• Maya 0492 615 370
• maya@tkwashandseal.com
• Please change the services:
• Hot/Cold Hi-Pressure Cleaning
• Sealing & Re-Sealing
• Roof Cleaning
• Colour Sealing
• Decorative Coatings
• Concrete Honing
• Thanks
Nice to have
• Something a bit different, something eye catching.l

```html
<!DOCTYPE html>
<html lang="en">
<head>
<meta charset="utf-8">
<title>T&amp;K's Pressure Cleaning – Business Card</title>
<link rel="stylesheet" href="https://fonts.googleapis.com/css2?family=Open+Sans:ital,wght@0,400;0,600;0,700;1,700&display=swap">
<style>
  :root {
    --backdrop: #a3a3a3;
    --card: #f3f3f4;
    --brand-red: #d40000;
    --ink-dark: #3a3a3a;
    --ink-mid: #555558;
    --rule: #b9b9bc;
    --band-text: #ffffff;
  }
  * { box-sizing: border-box; margin: 0; padding: 0; }
  html, body {
    width: 1105px; height: 1200px; overflow: hidden;
    background: var(--backdrop);
    font-family: "Open Sans", Arial, sans-serif;
  }
  .canvas { position: relative; width: 1105px; height: 1200px; }
  .card {
    position: absolute; left: 182px; width: 746px; height: 425px;
    background: var(--card); overflow: hidden;
  }
  .card--front { top: 120px; }
  .card--back  { top: 637px; }

  .brand {
    position: absolute; display: flex; align-items: center; gap: 12px;
    color: var(--ink-dark); font-weight: 600; font-size: 22px; line-height: 1.25;
  }
  .brand__mark {
    width: 18px; height: 18px; border-radius: 50%;
    background: var(--brand-red); flex: none;
  }
  .card--front .brand { left: 352px; top: 88px; width: 340px; }
  .card--back .brand { left: 203px; top: 168px; width: 340px; }

  .contact { position: absolute; top: 232px; }
  .contact--dylan { left: 38px; }
  .contact--maya  { left: 405px; }
  .contact__name {
    color: var(--brand-red); font-weight: 700; font-size: 27px; line-height: 32px;
  }
  .contact__phone {
    color: var(--ink-dark); font-weight: 600; font-size: 22px; line-height: 30px; margin-top: 6px;
  }
  .contact__line {
    color: var(--ink-mid); font-size: 19.5px; line-height: 27px; margin-top: 5px;
  }

  .rule {
    position: absolute; left: 0; right: 0; top: 382px; height: 2px; background: var(--rule);
  }
  .guarantee {
    position: absolute; left: 0; right: 0; bottom: 0; height: 39px;
    background: var(--brand-red); color: var(--band-text);
    font-style: italic; font-weight: 700; font-size: 19.5px;
    display: flex; align-items: center; justify-content: center;
  }

  .services {
    position: absolute; left: 0; right: 0; top: 300px; text-align: center;
    color: var(--ink-mid); font-size: 19px; line-height: 31px;
  }
  .services .dot { color: var(--brand-red); font-size: 13px; vertical-align: 2px; margin: 0 3px; }
  .quotes {
    position: absolute; left: 0; right: 0; top: 366px; text-align: center;
    color: var(--brand-red); font-style: italic; font-weight: 700; font-size: 23px;
  }
</style>
</head>
<body>
<main class="canvas">
  <section class="card card--front">
    <div class="brand"><span class="brand__mark"></span><span>T&amp;K's Pressure Cleaning &amp; Concrete Sealing</span></div>

    <div class="contact contact--dylan">
      <p class="contact__name">Dylan</p>
      <p class="contact__phone">0431 528 906</p>
      <p class="contact__line">dylan@tkwashandseal.com</p>
      <p class="contact__line">facebook.com/tkwashandseal</p>
    </div>
    <div class="contact contact--maya">
      <p class="contact__name">Maya</p>
      <p class="contact__phone">0492 615 370</p>
      <p class="contact__line">maya@tkwashandseal.com</p>
      <p class="contact__line">www.tkwashandseal.net</p>
    </div>

    <div class="rule"></div>
    <p class="guarantee">100% customer satisfaction guaranteed</p>
  </section>

  <section class="card card--back">
    <div class="brand"><span class="brand__mark"></span><span>T&amp;K's Pressure Cleaning &amp; Concrete Sealing</span></div>
    <p class="services">
      Hot/Cold Hi-Pressure Cleaning <span class="dot">●</span> Sealing &amp; Re-Sealing<br>
      Roof Cleaning <span class="dot">●</span> Colour Sealing <span class="dot">●</span> Decorative Coatings <span class="dot">●</span> Concrete Honing
    </p>
    <p class="quotes">Free no obligation quotes</p>
  </section>
</main>
</body>
</html>
```